Help design website for "Brightwater Civic Advisors" to advance the common good

Here is the Google doc link that lays out the design:

https://files.plumrivet.example/sheet/d/7QmTzR2wLx9KpVbN4hJcY8sEaUoFdG3iXkMnPq5rWt6/edit?usp=sharing

Here is the Google drive folder with the logos and photos: https://vault.plumrivet.example/open?id=4HkWp9LzQe2TxRvN8mBaYc3DsUoJfG6

The testimonials are being gathered and will be shared by Friday, 1/4.

The winner will also have to migrate the coding files to my hosting site.

Thank you for your help! Looking forward to seeing your designs.

Target Market(s)

Prospective clients

Industry/Entity Type

Non Profit

Coding

Coded - Design and coding required

Number of Pages Required

5+ page

Requirements
Must have
• Noted in the Google doc regarding layout.
Nice to have

```html
<!DOCTYPE html>
<html lang="en">
<head>
<meta charset="utf-8">
<title>Event Planning | Brightwater Civic Advisors</title>
<link href="https://fonts.googleapis.com/css2?family=Poppins:wght@500;600;700&family=Open+Sans:wght@400;600;700&display=swap" rel="stylesheet">
<style>
  :root {
    --brand-blue: #3d8bd0;
    --ink: #2a2a2a;
    --body-text: #444;
    --white: #ffffff;
    --footer-bg: #262832;
    --pattern-bg: #eff0f2;
    --divider: #4a4d58;
  }
  * { box-sizing: border-box; margin: 0; padding: 0; }
  html, body { width: 760px; height: 1200px; overflow: hidden; background: var(--white); }
  body { position: relative; font-family: "Open Sans", sans-serif; color: var(--body-text); }

  .site-header { position: absolute; top: 0; left: 0; width: 760px; height: 78px; background: var(--brand-blue); }
  .brand-name { position: absolute; left: 90px; top: 20px; width: 210px; font-family: "Poppins", sans-serif; font-weight: 600; font-size: 16px; line-height: 19px; letter-spacing: 2px; text-transform: uppercase; color: var(--white); }
  .cta-button { position: absolute; left: 466px; top: 13px; width: 203px; height: 26px; border: 2px solid var(--white); color: var(--white); font-family: "Poppins", sans-serif; font-weight: 600; font-size: 9px; display: flex; align-items: center; justify-content: center; text-decoration: none; }
  .main-nav { position: absolute; right: 91px; top: 55px; display: flex; gap: 20px; }
  .main-nav a { font-family: "Poppins", sans-serif; font-weight: 600; font-size: 8.5px; color: var(--white); text-decoration: none; padding-bottom: 2px; }
  .main-nav a.active { border-bottom: 1px solid var(--white); }

  .hero { position: absolute; top: 78px; left: 0; width: 760px; height: 352px; background: linear-gradient(180deg, #b0812e 0%, #8a5a2a 35%, #4a3a3c 70%, #2c2630 100%); }
  .hero-edge { position: absolute; top: 350px; left: 0; width: 760px; height: 80px; }

  .intro { position: absolute; top: 414px; left: 0; width: 760px; text-align: center; }
  .intro h1 { font-family: "Poppins", sans-serif; font-weight: 600; font-size: 16px; color: var(--ink); margin-bottom: 14px; }
  .intro p { font-size: 9.6px; line-height: 13px; width: 400px; margin: 0 auto; }

  .testimonial-card { position: absolute; top: 531px; width: 278px; height: 416px; background: var(--white); box-shadow: 0 2px 10px rgba(0,0,0,0.12); }
  .card-left { left: 90px; }
  .card-right { left: 390px; }
  .card-photo { position: relative; height: 226px; }
  .photo-award { background: linear-gradient(180deg, #8a6a40 0%, #5e3c22 55%, #2a1c14 100%); }
  .photo-stage { background: linear-gradient(180deg, #c9ccd0 0%, #7c8090 40%, #3e4258 75%, #1e1e26 100%); }
  .card-caption { position: absolute; left: 15px; right: 15px; bottom: 8px; font-family: "Poppins", sans-serif; font-weight: 700; font-size: 9.5px; line-height: 11.5px; text-transform: uppercase; color: var(--white); }
  .card-body { position: relative; padding: 20px 16px 0 32px; height: 190px; }
  .quote-mark { position: absolute; font-family: "Poppins", sans-serif; font-weight: 700; font-size: 22px; color: var(--ink); line-height: 1; }
  .quote-open { left: 17px; top: 18px; }
  .quote-close { font-size: 20px; vertical-align: -8px; margin-left: 3px; }
  .quote-text { font-size: 8.6px; line-height: 11.3px; color: var(--ink); }
  .attribution { position: absolute; left: 32px; bottom: 20px; width: 230px; font-size: 8.6px; line-height: 11.3px; color: var(--ink); }
  .attribution strong { font-weight: 700; }

  .pattern-band { position: absolute; top: 950px; left: 0; width: 760px; height: 115px; background: var(--pattern-bg); }
  .footer-shape { position: absolute; top: 995px; left: 0; width: 760px; height: 205px; }
  .site-footer { position: absolute; top: 1063px; left: 0; width: 760px; height: 137px; }
  .footer-brand { position: absolute; left: 92px; top: 22px; width: 260px; font-family: "Poppins", sans-serif; font-weight: 600; font-size: 19px; line-height: 22px; letter-spacing: 3px; text-transform: uppercase; color: var(--white); }
  .footer-divider { position: absolute; left: 388px; top: 13px; width: 1px; height: 90px; background: var(--divider); }
  .footer-menu { position: absolute; left: 425px; top: 25px; }
  .footer-menu h2 { font-family: "Poppins", sans-serif; font-weight: 700; font-size: 7.5px; color: var(--white); margin-bottom: 16px; }
  .footer-menu nav { font-size: 7.3px; color: var(--white); }
  .footer-menu nav a { color: var(--white); text-decoration: none; }
  .footer-menu nav span { margin: 0 6px; color: #9a9ca6; }
  .copyright { position: absolute; left: 426px; top: 86px; font-size: 7px; color: var(--white); }
</style>
</head>
<body>
  <header class="site-header">
    <div class="brand-name">Brightwater Civic Advisors</div>
    <a class="cta-button" href="#">BOOK A COMPLIMENTARY CONSULTATION</a>
    <nav class="main-nav">
      <a href="#">ABOUT</a>
      <a href="#" class="active">SERVICES &amp; TESTIMONIALS</a>
      <a href="#">MEDIA &amp; IMPACT</a>
      <a href="#">CONTACT</a>
    </nav>
  </header>

  <div class="hero" role="img" aria-label="Photo of students and staff applauding around a speaker at a podium during an event"></div>
  <svg class="hero-edge" viewBox="0 0 760 80" preserveAspectRatio="none" aria-hidden="true">
    <polygon points="0,68 380,10 760,70 760,80 0,80" fill="#3d8bd0"/>
    <polygon points="0,75 380,17 760,77 760,80 0,80" fill="#ffffff"/>
  </svg>

  <section class="intro">
    <h1>Event Planning</h1>
    <p>Dana has planned events of all sizes that bring together students, staff, faculty, alumni, community partners, leaders and residents for dialogue and service.</p>
  </section>

  <article class="testimonial-card card-left">
    <div class="card-photo photo-award" role="img" aria-label="Photo of Dana presenting an award plaque to a graduate at a reception">
      <div class="card-caption">Dana presenting the “Harriet Vale Alumni Community Impact Award” at annual awards reception</div>
    </div>
    <div class="card-body">
      <span class="quote-mark quote-open">“</span>
      <p class="quote-text">Our team is grateful for Dana’s significant contributions to the Larkspur Global Youth Forum’s (LGYF) Day of Action at the University of Eastbrook. She organized one of the most successful service projects for our program to date, allowing 1,000 LGYF students from around the world the opportunity to work with and learn from the extraordinary nonprofits in the South Side Eastbrook community.<span class="quote-mark quote-close">”</span></p>
      <p class="attribution"><strong>Nora Whitfield,</strong> Community Engagement Manager, Larkspur Global Forum at the Larkspur Foundation</p>
    </div>
  </article>

  <article class="testimonial-card card-right">
    <div class="card-photo photo-stage" role="img" aria-label="Photo of Dana speaking on stage before a large crowd in a gymnasium">
      <div class="card-caption">Dana providing open remarks for Larkspur Foundation Day of Action</div>
    </div>
    <div class="card-body">
      <p class="attribution" style="bottom:22px"><strong>Joanna Pell</strong>&nbsp; Community Engagement Manager, Meals Forward</p>
    </div>
  </article>

  <div class="pattern-band" role="img" aria-label="Decorative background pattern"></div>
  <svg class="footer-shape" viewBox="0 0 760 205" preserveAspectRatio="none" aria-hidden="true">
    <polygon points="0,68 380,0 760,68 760,205 0,205" fill="#262832"/>
  </svg>

  <footer class="site-footer">
    <div class="footer-brand">Brightwater Civic Advisors</div>
    <div class="footer-divider"></div>
    <div class="footer-menu">
      <h2>MENU</h2>
      <nav>
        <a href="#">ABOUT</a><span>|</span><a href="#">SERVICES &amp; TESTIMONIALS</a><span>|</span><a href="#">MEDIA &amp; IMPACT</a><span>|</span><a href="#">CONTACT</a>
      </nav>
    </div>
    <p class="copyright">Copyrights @ 2019 All Rights Reserved</p>
  </footer>
</body>
</html>
```